Business card design Needed for new logo / Construction business, home extensions and new builds

We need a business card design using our new logo files which i will attach to this project :)

We are a small construction business specialising in home extensions, new builds and property development. We are very ambitious and would appreciate professional and elegant designs for our new business card.

Very serious about using the services on MakerQuarry and recently acquired our new logo from here :)

Please get involved, i will feedback when i can as i am very busy but can respond daily, thanks

Target Market(s)

People that want to build onto their houses, new building developments or adding too their existing property

Industry/Entity Type

Construction

Contact Information for Business Card

Renwick Tolliver Construction, Lionel Ashby (Managing Director), Tel 07822254961, email - info@renwick-tolliver, www.renwick-tolliver.co.uk

Colors

Designer to choose colors to be used in the design.

Requirements
Must have
• I like a deep grey on the back please. A lot of you have provided black from and back, try mixing things up a little. The black looks cool 😎 Thanks

```html
<!DOCTYPE html>
<html lang="en">
<head>
<meta charset="utf-8">
<title>Renwick Tolliver Construction – Business Card</title>
<link href="https://fonts.googleapis.com/css2?family=Cinzel:wght@500&family=Lato:wght@400&display=swap" rel="stylesheet">
<style>
  :root {
    --stage: #141414;
    --card-front: #1c1c1c;
    --card-back: #3a3a3b;
    --gold: #d4a12a;
    --gold-light: #f0c75a;
    --text-soft: #e2e2e2;
  }
  * { margin: 0; padding: 0; box-sizing: border-box; }
  html, body {
    width: 1200px; height: 875px; overflow: hidden;
    background: var(--stage);
  }
  .stage {
    width: 1200px; height: 875px;
    display: flex; align-items: center; justify-content: center; gap: 50px;
  }
  .card {
    width: 525px; height: 300px;
    border-radius: 16px;
    position: relative;
    box-shadow: 0 18px 40px rgba(0,0,0,.55);
  }
  /* Front */
  .card-front {
    background: var(--card-front);
    display: flex; flex-direction: column; align-items: center; justify-content: center;
  }
  .brand {
    display: flex; align-items: center; gap: 14px;
  }
  .brand-square {
    width: 14px; height: 14px; background: var(--gold); flex: none;
  }
  .brand-name {
    font-family: 'Cinzel', serif; font-weight: 500;
    color: var(--gold);
    font-size: 27px; letter-spacing: 1.5px;
    text-align: center; line-height: 1.35;
  }
  .brand-rule {
    display: flex; align-items: center; gap: 10px; margin-top: 14px;
  }
  .brand-rule span {
    display: block; width: 60px; height: 2px;
    background: linear-gradient(90deg, transparent, var(--gold));
  }
  .brand-rule span:last-child {
    background: linear-gradient(90deg, var(--gold), transparent);
  }
  /* Back */
  .card-back {
    background: var(--card-back);
  }
  .back-brand {
    position: absolute; top: 30px; right: 34px;
    display: flex; align-items: center; gap: 8px;
  }
  .back-brand .brand-square { width: 9px; height: 9px; }
  .back-brand .brand-name { font-size: 13px; letter-spacing: 1px; }
  .holder {
    position: absolute; left: 34px; top: 136px;
  }
  .holder-name {
    font-family: 'Cinzel', serif; font-weight: 500;
    color: var(--gold); font-size: 22px; letter-spacing: 1px; line-height: 1.2;
  }
  .holder-role {
    font-family: 'Lato', sans-serif; font-weight: 400;
    color: var(--text-soft); font-size: 13px; margin-top: 3px;
  }
  .gold-rule {
    position: absolute; left: 34px; right: 34px; top: 200px;
    height: 1.5px;
    background: linear-gradient(90deg, var(--gold), var(--gold-light) 50%, var(--gold));
  }
  .contacts {
    position: absolute; left: 34px; top: 212px;
    list-style: none;
    font-family: 'Lato', sans-serif; font-weight: 400;
    color: var(--text-soft); font-size: 12.5px;
  }
  .contacts li {
    display: flex; align-items: center; gap: 9px; height: 21px;
  }
  .contacts svg { width: 12px; height: 12px; flex: none; }
  .icon-fill { fill: var(--gold); }
  .icon-line { fill: none; stroke: var(--gold); stroke-width: 2; }
</style>
</head>
<body>
<main class="stage">
  <section class="card card-front" aria-label="Card front">
    <div class="brand">
      <span class="brand-square"></span>
      <h1 class="brand-name">Renwick Tolliver<br>Construction</h1>
    </div>
    <div class="brand-rule"><span></span><span></span></div>
  </section>

  <section class="card card-back" aria-label="Card back">
    <div class="back-brand">
      <span class="brand-square"></span>
      <span class="brand-name">Renwick Tolliver</span>
    </div>
    <div class="holder">
      <h2 class="holder-name">LIONEL ASHBY</h2>
      <p class="holder-role">Managing Director</p>
    </div>
    <div class="gold-rule"></div>
    <ul class="contacts">
      <li>
        <svg viewBox="0 0 24 24" aria-hidden="true"><path class="icon-fill" d="M6.6 10.8a15.1 15.1 0 0 0 6.6 6.6l2.2-2.2a1 1 0 0 1 1-.25 11.4 11.4 0 0 0 3.6.57 1 1 0 0 1 1 1V20a1 1 0 0 1-1 1A17 17 0 0 1 3 4a1 1 0 0 1 1-1h3.5a1 1 0 0 1 1 1c0 1.25.2 2.45.57 3.57a1 1 0 0 1-.25 1z"/></svg>
        07822254961
      </li>
      <li>
        <svg viewBox="0 0 24 24" aria-hidden="true"><path class="icon-line" d="M2 5h20v14H2z M2 5l10 8 10-8"/></svg>
        info@renwick-tolliver.co.uk
      </li>
      <li>
        <svg viewBox="0 0 24 24" aria-hidden="true"><circle class="icon-line" cx="12" cy="12" r="9"/><path class="icon-line" d="M3 12h18M12 3c3 3 3 15 0 18M12 3c-3 3-3 15 0 18"/></svg>
        renwick-tolliver.co.uk
      </li>
    </ul>
  </section>
</main>
</body>
</html>
```